Slow Winter Song. A CD of beautiful 17th century music for lute played by a world famous lutenist.

Hi designers,
My name is Ollie Pellicott and I am an international lute player in need of a CD cover design. I am blind, so will be relying on other people's eyes and descriptions during the process, including yours! Are you up for the challenge?
My CD is called Slow Winter Song. It's beautiful lute music from the 17th century, very intimate and carming, but also very powerful.
I would like you to use the attached image, and find a way to include the following text in a tasteful way:
The text for the front cover is as follows:
Slow Winter Song
Oliver Pellicott - lute and theorbo
Music by Harcrane, Fennimore, Brackley, Tarn, Cavallenti and Ruhlendorf.
Here is a viewora link to some of the music I play, which should give you an idea:
www.viewora.net/olliepellicott1
Here is a link to my website, where you can see the covers of my other CDs, and get more information about me:
www.oliverpellicott.net
I'm excited to receive your design and ideas.
Best wishes
Ollie

```html
<!DOCTYPE html>
<html lang="en">
<head>
<meta charset="utf-8">
<title>Slow Winter Song – CD Cover</title>
<link rel="stylesheet" href="https://fonts.googleapis.com/css2?family=Mrs+Saint+Delafield&family=Michroma&display=swap">
<style>
  :root {
    --night-deep: #1a1410;
    --night-umber: #4a3a2c;
    --candle-amber: #b08a5e;
    --smoke-grey: #8d8a86;
    --band-veil: rgba(200, 198, 195, 0.42);
    --ink: #111010;
    --paper-white: #f4f2ee;
  }
  html, body {
    margin: 0;
    padding: 0;
    width: 1200px;
    height: 1200px;
    overflow: hidden;
    background: var(--night-deep);
  }
  .cover {
    position: relative;
    width: 1200px;
    height: 1200px;
    overflow: hidden;
  }
  .cover-artwork {
    position: absolute;
    inset: 0;
    background:
      radial-gradient(circle at 72% 42%, rgba(255, 240, 210, 0.55) 0 3%, transparent 14%),
      radial-gradient(ellipse at 30% 75%, rgba(214, 160, 96, 0.75) 0 12%, transparent 34%),
      radial-gradient(ellipse at 50% 25%, rgba(176, 138, 94, 0.6), transparent 55%),
      linear-gradient(180deg, var(--night-umber) 0%, #5e4c3d 45%, #2a211b 70%, var(--night-deep) 100%);
  }
  .cover-artwork::after {
    content: "";
    position: absolute;
    left: 906px;
    top: 0;
    right: 0;
    bottom: 0;
    background: rgba(10, 8, 6, 0.35);
  }
  .title-band {
    position: absolute;
    top: 0;
    bottom: 0;
    left: 285px;
    width: 621px;
    background: var(--band-veil);
  }
  .album-title {
    position: absolute;
    left: 285px;
    width: 621px;
    top: 40px;
    margin: 0;
    font-family: "Mrs Saint Delafield", cursive;
    font-weight: 400;
    font-size: 190px;
    line-height: 210px;
    color: var(--ink);
    text-align: center;
  }
  .album-title span { display: block; }
  .performer {
    position: absolute;
    left: 285px;
    width: 621px;
    top: 762px;
    margin: 0;
    font-family: "Michroma", sans-serif;
    font-size: 24px;
    line-height: 38px;
    letter-spacing: 3px;
    color: var(--paper-white);
    text-align: center;
    text-transform: uppercase;
  }
  .performer span { display: block; }
  .subtitle {
    position: absolute;
    left: 285px;
    width: 621px;
    top: 895px;
    margin: 0;
    font-family: "Mrs Saint Delafield", cursive;
    font-size: 62px;
    color: var(--ink);
    text-align: center;
  }
  .composers {
    position: absolute;
    left: 260px;
    width: 671px;
    top: 988px;
    margin: 0;
    font-family: "Michroma", sans-serif;
    font-size: 21px;
    line-height: 29px;
    letter-spacing: 1px;
    color: var(--paper-white);
    text-align: center;
    text-transform: uppercase;
  }
  .composers span { display: block; }
  .dot {
    display: inline-block;
    width: 11px;
    height: 11px;
    border-radius: 50%;
    background: var(--paper-white);
    margin: 0 8px;
    vertical-align: 2px;
  }
</style>
</head>
<body>
  <main class="cover">
    <div class="cover-artwork" role="img" aria-label="Painting of a lute leaning against a candlelit table in a dim, warm-toned room"></div>
    <div class="title-band"></div>

    <h1 class="album-title"><span>Slow</span><span>Winter</span><span>Song</span></h1>

    <p class="performer"><span>Oliver Pellicott</span><span>Lute and Theorbo</span></p>

    <p class="subtitle">17th century music for lute</p>

    <p class="composers">
      <span>Music by:</span>
      <span>Harcrane<i class="dot"></i>Fennimore<i class="dot"></i>Brackley</span>
      <span>Tarn<i class="dot"></i>Cavallenti<i class="dot"></i>Ruhlendorf</span>
    </p>
  </main>
</body>
</html>
```